Coastline Premier Retreats Business Card Design

Design a business card for Coastline Premier Retreats. Look at the website for colors and reference. Card should have logo, name, title, office number, mobile number, email, URL and a tagline like, "Luxury Hotel & Resort Email Marketing" (This might change).

https://www.coastlinepremierretreats.example

The rest I will leave up to your imagination.

Contact Information for Business Card

Logo, name, title, office number, mobile number, email, URL and a tagline like, "Luxury Hotel & Resort Email Marketing" (This might change).

```html
<!DOCTYPE html>
<html lang="en">
<head>
<meta charset="utf-8">
<title>Coastline Premier Retreats – Business Card</title>
<link rel="stylesheet" href="https://fonts.googleapis.com/css2?family=Michroma&family=Open+Sans:wght@400;700&display=swap">
<style>
  :root {
    --backdrop: #3b3b3b;
    --card: #1b1b1b;
    --accent: #f07a1e;
    --ink: #ffffff;
    --ink-soft: #d9d9d9;
    --emboss: #9a9a9a;
  }
  * { box-sizing: border-box; margin: 0; padding: 0; }
  html, body {
    width: 1200px; height: 801px; overflow: hidden;
    background: var(--backdrop);
  }
  .stage { position: relative; width: 1200px; height: 801px; }
  .card {
    position: absolute; width: 540px; height: 309px;
    background: var(--card);
    border-left: 2px solid var(--accent);
    border-bottom: 2px solid var(--accent);
    box-shadow: 0 18px 40px rgba(0,0,0,.45);
  }
  .card--front { left: 60px; top: 80px; }
  .card--back { left: 600px; top: 410px; }

  .brand {
    position: absolute; left: 40px; top: 96px;
    display: flex; align-items: center; gap: 12px;
  }
  .brand__mark { width: 14px; height: 14px; background: var(--accent); }
  .brand__name {
    font-family: "Michroma", sans-serif; font-size: 17px; line-height: 1.25;
    color: var(--ink); letter-spacing: 1px; text-transform: uppercase;
  }

  .person { position: absolute; right: 36px; top: 96px; text-align: left; }
  .person__name {
    font-family: "Open Sans", sans-serif; font-weight: 700; font-size: 21px;
    color: var(--accent); text-transform: uppercase; letter-spacing: .5px;
  }
  .person__title {
    font-family: "Open Sans", sans-serif; font-size: 13px; color: var(--ink-soft);
    margin-top: 2px; padding-left: 60px;
  }

  .divider {
    position: absolute; left: 40px; right: 36px; top: 190px;
    height: 1px; background: var(--accent);
  }

  .contacts { position: absolute; left: 40px; top: 206px; list-style: none; }
  .contacts li {
    display: flex; align-items: center; gap: 10px;
    font-family: "Open Sans", sans-serif; font-size: 14px; color: var(--ink-soft);
    line-height: 24px;
  }
  .contacts svg { width: 11px; height: 11px; flex: none; }

  .back-brand {
    position: absolute; left: 0; right: 0; top: 92px; text-align: center;
    font-family: "Michroma", sans-serif; font-size: 27px; line-height: 1.25;
    color: var(--emboss); letter-spacing: 2px; text-transform: uppercase;
  }
  .tagline {
    position: absolute; left: 36px; bottom: 34px;
    font-family: "Michroma", sans-serif; font-size: 13px; color: var(--ink);
    letter-spacing: 3px; text-transform: uppercase;
  }
</style>
</head>
<body>
<main class="stage">
  <section class="card card--front">
    <div class="brand">
      <span class="brand__mark"></span>
      <span class="brand__name">Coastline<br>Premier Retreats</span>
    </div>
    <div class="person">
      <p class="person__name">Darion Welker</p>
      <p class="person__title">President / CEO</p>
    </div>
    <div class="divider"></div>
    <ul class="contacts">
      <li>
        <svg viewBox="0 0 12 12"><path fill="var(--accent)" d="M2.5 1l2 2.2-1 1.3c.7 1.5 1.8 2.6 3.3 3.3l1.3-1 2.2 2-1.2 1.6C5 10.2 1.8 7 .9 2.2z"/></svg>
        555.014.2290
      </li>
      <li>
        <svg viewBox="0 0 12 12"><rect x="0.5" y="2" width="11" height="8" fill="var(--accent)"/><path d="M1 2.5l5 4 5-4" stroke="var(--card)" fill="none"/></svg>
        info@coastlinepremierretreats.example
      </li>
      <li>
        <svg viewBox="0 0 12 12"><circle cx="6" cy="6" r="5.5" fill="var(--accent)"/><path d="M.5 6h11M6 .5c-2.5 3-2.5 8 0 11M6 .5c2.5 3 2.5 8 0 11" stroke="var(--card)" stroke-width=".8" fill="none"/></svg>
        www.coastlinepremierretreats.example
      </li>
    </ul>
  </section>

  <section class="card card--back">
    <p class="back-brand">Coastline<br>Premier Retreats</p>
    <p class="tagline">Luxury Hotel &amp; Resort Email Marketing</p>
  </section>
</main>
</body>
</html>
```